Marrowind Holiday Retreat Flyer Project

Flyer required for a holiday caravan park. I have attached the current flyer for the park and would like to use the same layout. Please also alter the changes to the text that I have marked up. Until the additional uploads for the new images are ready, could you please just leave those as a blank square and the images can be inserted once I have them loaded.

Target Market(s)

Holiday makers

Industry/Entity Type

Tourism

Colors
3176b5
33a6d7
0393ce
fbee3e
fbed22
ffffff
faa54b

Requirements
Must have
• copy the attached flyer
• Would like a better title font for the front text - "Marrowind Holiday Retreat", please make that a more playful holiday feel font
• Please use images 001 & 002 as the front cover images
• I have more images to load up which will be done 4/7.
Nice to have
• would like a better colour back ground to the flyer, maybe blue-ish and then alter the colour of the text accordingly
Should not have
• Please use the attached flyer copy as a template

```html
<!DOCTYPE html>
<html lang="en">
<head>
<meta charset="utf-8">
<title>Marrowind Holiday Retreat – Flyer</title>
<link rel="stylesheet" href="https://fonts.googleapis.com/css2?family=Fredoka:wght@600&family=Josefin+Sans:wght@600&family=Montserrat:wght@400;500;600;700&family=Catamaran:wght@700;800&display=swap">
<style>
:root{
  --navy:#1f4e8c;
  --blue:#3176b5;
  --text-blue:#2a6bb3;
  --sky:#33a6d7;
  --teal:#3fb6d3;
  --pale:#e8f5fb;
  --mist:#bfe3f4;
  --ink:#1b2a3a;
  --white:#ffffff;
  --stage:#3a3b3d;
}
*{box-sizing:border-box;margin:0;padding:0}
html,body{width:784px;height:1200px;overflow:hidden}
body{background:var(--stage);font-family:"Montserrat",sans-serif;color:var(--ink);position:relative}
.sheet{position:absolute;left:6px;width:772px;height:582px;overflow:hidden;
  background:linear-gradient(160deg,var(--white) 0%,var(--pale) 45%,var(--mist) 100%);
  box-shadow:0 4px 14px rgba(0,0,0,.55)}
.sheet-outside{top:8px}
.sheet-inside{top:604px}
.abs{position:absolute}
.deco{position:absolute;left:0;top:0;width:772px;height:582px}

/* outside – left panel */
.map-area{left:-40px;top:-78px;width:280px;height:280px;border-radius:50%;
  background:radial-gradient(circle at 40% 55%,#bfe07a 0%,#9fd06a 40%,#4cc0d6 70%,#3fb6d3 100%);
  border:4px solid var(--blue)}
.intro{left:18px;top:222px;width:212px;font-size:9.4px;line-height:14.6px;font-weight:600;
  color:var(--text-blue);text-align:justify}
.band{height:23px;display:flex;align-items:center;
  background:linear-gradient(90deg,var(--teal) 0%,#9ad9ea 70%,rgba(255,255,255,0) 100%);
  font-family:"Catamaran",sans-serif;font-weight:800;color:var(--ink)}
.band-activities{left:0;top:326px;width:248px;padding-left:22px;font-size:12.5px}
.activity-list{list-style:none;font-size:8.4px;font-weight:600;color:var(--ink);line-height:10px}
.activity-list li{margin-bottom:6.8px}
.activities-a{left:18px;top:366px;width:128px}
.activities-b{left:152px;top:366px;width:96px}
.col-rule{left:145px;top:362px;width:1.5px;height:110px;background:var(--blue)}
.attractions{left:0;top:484px;width:248px;height:82px;background:rgba(255,255,255,.45);
  display:flex;align-items:center;justify-content:center;text-align:center;
  font-family:"Catamaran",sans-serif;font-weight:800;font-size:18px;line-height:19.5px;color:var(--navy)}

/* titles */
.brand-name{font-family:"Fredoka",sans-serif;font-weight:600;letter-spacing:1px;line-height:1}
.brand-sub{font-family:"Josefin Sans",sans-serif;font-weight:600;letter-spacing:3.2px;line-height:1}
.title-mid{left:248px;top:200px;width:264px;text-align:center}
.title-mid .brand-name{font-size:32px;color:var(--navy)}
.title-mid .brand-sub{font-size:15px;color:var(--ink);margin-top:5px}
.title-cover{left:512px;top:50px;width:260px;text-align:center}
.title-cover .brand-name{font-size:32px;color:var(--white)}
.title-cover .brand-sub{font-size:15px;color:var(--navy);margin-top:5px}

/* contacts */
.contact{list-style:none;font-size:11px;font-weight:500;letter-spacing:.4px;color:var(--ink)}
.contact li{display:flex;align-items:center;gap:9px;height:17px}
.contact li.web{margin-top:15px;font-size:12px}
.contact svg{width:12px;height:12px;flex:none}
.contact-mid{left:269px;top:356px}
.contact-cover{left:537px;top:482px}

/* cover panel */
.cover-panel{left:512px;top:0;width:260px;height:582px;
  background:linear-gradient(180deg,#3d7cc2 0%,#4a8fcf 55%,#8cd0ee 100%)}
.photo{background:linear-gradient(160deg,#7fb8dc,#3e86b8 60%,#5d7c8c)}
.photo-jump{left:512px;top:134px;width:260px;height:218px}
.photo-pier{left:588px;top:282px;width:188px;height:188px;border-radius:50%;
  border:4px solid var(--navy);outline:3px solid var(--white);
  background:linear-gradient(160deg,#cfe6f2,#8ab3c6 50%,#6c6a5c)}

/* inside – panel 1 */
.band-todo{left:0;top:36px;width:248px;padding-left:30px;font-size:18px}
.lead{font-size:11.6px;line-height:14px;color:var(--sky);font-weight:500}
.lead-estuary{left:30px;top:80px;width:200px}
.lead-beach{left:30px;top:176px;width:200px}
.lead-sport{left:30px;top:286px;width:210px}
.todo-list{list-style:none;font-size:9.4px;font-weight:600;line-height:13px;color:var(--ink)}
.rule{height:2px;background:var(--teal)}
.rule-1{left:0;top:163px;width:256px}
.rule-2{left:0;top:276px;width:256px}

/* inside – panel 2 */
.band-stay{left:248px;top:196px;width:260px;padding-left:26px;font-size:18px}
.plain-list{list-style:none;font-size:12px;font-weight:500;line-height:22.6px;color:var(--ink)}
.stay-list{left:275px;top:234px}

/* inside – panel 3 */
.band-facilities{left:512px;top:24px;width:260px;padding-left:24px;font-size:18px}
.fac-a{left:536px;top:80px}
.fac-b{left:672px;top:80px}
.fac-rule{left:649px;top:84px;width:1.5px;height:86px;background:var(--blue)}
.nearby{left:537px;top:180px;list-style:none;font-size:10px;font-weight:700;
  line-height:17.6px;color:var(--blue)}
.footer-note{left:518px;top:521px;font-size:10.6px;line-height:13.5px;font-weight:500;color:var(--ink)}
.footer-contact{left:518px;top:556px;display:flex;gap:12px;font-size:9px;font-weight:500;align-items:center}
.footer-contact span{display:flex;align-items:center;gap:4px}
.footer-contact svg{width:11px;height:11px}
</style>
</head>
<body>

<svg width="0" height="0" style="position:absolute">
  <defs>
    <symbol id="ic-phone" viewBox="0 0 24 24"><circle cx="12" cy="12" r="12" fill="#3176b5"/><path d="M8 6.5c.6-.5 1.3-.4 1.7.2l1 1.6c.3.5.2 1.1-.2 1.5l-.7.6c.6 1.3 1.6 2.4 2.9 3l.6-.7c.4-.4 1-.5 1.5-.2l1.6 1c.6.4.7 1.1.2 1.7l-.8.9c-.7.7-1.8.9-2.8.4-2.7-1.3-4.800-3.4-6-6.1-.4-1-.2-2.1.5-2.8z" fill="#fff"/></symbol>
    <symbol id="ic-pin" viewBox="0 0 24 24"><circle cx="12" cy="12" r="12" fill="#3176b5"/><path d="M12 5a4.5 4.5 0 0 0-4.5 4.5C7.5 13 12 19 12 19s4.5-6 4.5-9.5A4.5 4.5 0 0 0 12 5z" fill="#fff"/><circle cx="12" cy="9.6" r="1.7" fill="#3176b5"/></symbol>
    <symbol id="ic-mail" viewBox="0 0 24 24"><circle cx="12" cy="12" r="12" fill="#3176b5"/><rect x="6.5" y="8" width="11" height="8" rx="1" fill="#fff"/><path d="M6.8 8.4 12 12.4l5.2-4" stroke="#3176b5" stroke-width="1.2" fill="none"/></symbol>
    <symbol id="ic-web" viewBox="0 0 24 24"><circle cx="12" cy="12" r="12" fill="#3176b5"/><circle cx="12" cy="12" r="5.5" fill="none" stroke="#fff" stroke-width="1.3"/><path d="M6.5 12h11M12 6.5c-2.2 3-2.2 8 0 11M12 6.5c2.2 3 2.2 8 0 11" stroke="#fff" stroke-width="1.1" fill="none"/></symbol>
  </defs>
</svg>

<!-- Outside of the trifold -->
<section class="sheet sheet-outside">
  <svg class="deco" viewBox="0 0 772 582" aria-hidden="true">
    <path d="M248 322 C330 300 420 296 512 340 L512 582 L248 582 Z" fill="#9fd6ef" opacity=".55"/>
    <path d="M248 312 C330 290 420 286 512 332" stroke="#ffffff" stroke-width="5" fill="none" opacity=".8"/>
  </svg>

  <div class="abs map-area" role="img" aria-label="Stylised location map showing the retreat between the estuary and the beach"></div>
  <p class="abs intro">We are the second turn to left, after the bridge. Ideally located nestled between Pelham Beach and the Estuary, 3-minutes south of the Marrowind cut with all the associated water activities and 15-minutes from Kellsmouth CBD boasting.</p>

  <div class="abs band band-activities">A RANGE OF ACTIVITIES SUCH AS</div>
  <ul class="abs activity-list activities-a">
    <li>SUMMER CONCERTS</li><li>DOLPHIN TOURS</li><li>MOVIE THEATRES</li><li>SUBERB RESTAURANTS</li><li>TIDEWATER MARKETS</li><li>KELLSMOUTH PERFORMING<br>ARTS CENTRE</li>
  </ul>
  <div class="abs col-rule"></div>
  <ul class="abs activity-list activities-b">
    <li>WINERIES</li><li>WILDLIFE PARKS</li><li>TAVERNS</li><li>NIGHT CLUBS</li><li>FESTIVALS</li><li>ART GALLERY</li>
  </ul>
  <div class="abs attractions">HISTORICAL SITES AND<br>MANY MORE TOURIST<br>ATTRACTIONS!</div>

  <div class="abs title-mid">
    <div class="brand-name">MARROWIND</div>
    <div class="brand-sub">HOLIDAY RETREAT</div>
  </div>
  <ul class="abs contact contact-mid">
    <li><svg><use href="#ic-phone"/></svg>(08) 9470 2263</li>
    <li><svg><use href="#ic-pin"/></svg>42 Shoreline Rd. Marrowind 6214</li>
    <li><svg><use href="#ic-mail"/></svg>info@marrowindretreat.com.au</li>
    <li class="web"><svg><use href="#ic-web"/></svg>www.marrowindretreat.com.au</li>
  </ul>

  <div class="abs cover-panel"></div>
  <div class="abs title-cover">
    <div class="brand-name">MARROWIND</div>
    <div class="brand-sub">HOLIDAY RETREAT</div>
  </div>
  <div class="abs photo photo-jump" role="img" aria-label="Cover photo: children jumping off a houseboat into the water"></div>
  <svg class="deco" viewBox="0 0 772 582" aria-hidden="true">
    <path d="M512 352 L512 330 C580 360 640 372 700 340 L772 318 L772 380 C700 400 600 390 512 352 Z" fill="#6fb7e3"/>
    <path d="M512 340 C590 372 650 380 772 330" stroke="#ffffff" stroke-width="3" fill="none" opacity=".7"/>
  </svg>
  <div class="abs photo-pier" role="img" aria-label="Cover photo: family crabbing from a wooden jetty"></div>
  <ul class="abs contact contact-cover">
    <li><svg><use href="#ic-phone"/></svg>(08) 9470 2263</li>
    <li><svg><use href="#ic-pin"/></svg>42 Shoreline Rd. Marrowind 6214</li>
    <li><svg><use href="#ic-mail"/></svg>info@marrowindretreat.com.au</li>
    <li class="web"><svg><use href="#ic-web"/></svg>www.marrowindretreat.com.au</li>
  </ul>
</section>

<!-- Inside of the trifold -->
<section class="sheet sheet-inside">
  <div class="abs band band-todo">WHAT TO DO?</div>
  <p class="abs lead lead-estuary">The Estuary is only 2-minutes<br>to the east for:</p>
  <ul class="abs todo-list" style="left:30px;top:114px">
    <li>WATER SPORTS</li><li>CRABBING</li><li>BOAT RAMP ACCESS</li>
  </ul>
  <ul class="abs todo-list" style="left:154px;top:114px">
    <li>SWIMMING</li><li>PRAWNING</li><li>BOATING</li>
  </ul>
  <div class="abs rule rule-1"></div>

  <p class="abs lead lead-beach">Pelham Beach is 5-minutes<br>to the west for:</p>
  <ul class="abs todo-list" style="left:30px;top:210px">
    <li>WATER SKIING</li><li>SWIMMING</li><li>BEACH WALKING</li><li>BOAT RAMP ACCESS</li>
  </ul>
  <ul class="abs todo-list" style="left:154px;top:210px">
    <li>CRABBING</li><li>SAILING</li><li>FISHING</li><li>SURFING</li>
  </ul>
  <div class="abs rule rule-2"></div>

  <p class="abs lead lead-sport">Sporting Facilities 5-minutes</p>
  <ul class="abs todo-list" style="left:98px;top:306px">
    <li>GOLFING</li><li>BOWLS</li>
  </ul>

  <svg class="deco" viewBox="0 0 772 582">
    <defs>
      <linearGradient id="g-sunset" x1="0" y1="0" x2="0" y2="1">
        <stop offset="0" stop-color="#3a4a63"/><stop offset=".12" stop-color="#e59a45"/><stop offset=".3" stop-color="#2c3d55"/><stop offset="1" stop-color="#0f1c2c"/>
      </linearGradient>
      <linearGradient id="g-aerial" x1="0" y1="0" x2="1" y2="1">
        <stop offset="0" stop-color="#3f96c2"/><stop offset=".5" stop-color="#8a9a78"/><stop offset="1" stop-color="#2f8cbc"/>
      </linearGradient>
    </defs>
    <path role="img" aria-label="Photo: sunset over the water with people fishing from the shore"
      d="M248 0 H510 V160 C470 126 420 120 380 144 C330 174 290 178 248 168 Z" fill="url(#g-sunset)"/>
    <path d="M248 168 C290 178 330 174 380 144 C420 120 470 126 510 160" stroke="#ffffff" stroke-width="4" fill="none"/>
    <path role="img" aria-label="Photo: resort swimming pool"
      d="M0 350 C60 330 120 342 180 348 C215 351 240 340 262 328 L262 582 L0 582 Z" fill="#4fa3b8"/>
    <path d="M0 340 C60 320 120 334 180 340 C215 343 240 330 262 318" stroke="#ffffff" stroke-width="4" fill="none"/>
    <path role="img" aria-label="Photo: aerial view of the estuary, canals and bridge"
      d="M512 318 C560 290 600 300 640 320 C690 346 730 322 772 300 L772 516 C700 502 600 506 512 518 Z" fill="url(#g-aerial)"/>
    <path d="M512 312 C560 284 600 294 640 314 C690 340 730 316 772 294" stroke="#3fb6d3" stroke-width="4" fill="none"/>
    <circle role="img" aria-label="Photo: dolphin leaping out of the water" cx="340" cy="498" r="144" fill="#3f8fc8" stroke="#3fb6d3" stroke-width="5"/>
    <circle role="img" aria-label="Photo: two-storey holiday chalets" cx="436" cy="404" r="72" fill="#a9cde6" stroke="#3fb6d3" stroke-width="5"/>
  </svg>

  <div class="abs band band-stay">ACCOMODATION</div>
  <ul class="abs plain-list stay-list">
    <li>Chalets Ensuite &amp; Air Con</li><li>Caravans</li><li>Caravans Ensuite &amp; Air Con</li><li>Powered SItes</li>
  </ul>

  <div class="abs band band-facilities">FACILITIES</div>
  <ul class="abs plain-list fac-a"><li>EFTPOS</li><li>Swimming Pool</li><li>Undercover BBQ</li><li>Crab Cooker</li></ul>
  <div class="abs fac-rule"></div>
  <ul class="abs plain-list fac-b"><li>Playground</li><li>Laundrette</li><li>TV Room</li><li>Games Room</li></ul>
  <ul class="abs nearby">
    <li>2 SUPERMARKETS WITHIN 2-MINUTES</li>
    <li>13 TAKE-AWAY SHOPS WITHIN 7-MINUTES</li>
    <li>6 RESTAURANTS WITHIN 7-MINUTES</li>
    <li>KELLSMOUTH CBD 15-MINUTES</li>
  </ul>

  <p class="abs footer-note">For more informations,<br>please contact us or visit our website:</p>
  <div class="abs footer-contact">
    <span><svg><use href="#ic-phone"/></svg>(08) 9470 2263</span>
    <span><svg><use href="#ic-web"/></svg>www.marrowindretreat.com.au</span>
  </div>
</section>

</body>
</html>
```